The Aldermoor- outdoor banner

This should be a horizontal banner. It should have the logos attached incorporated and the following details
Coming Spring 2025: The Aldermoor - Exclusive Luxury Condos
Listed by Marisol Quennell | Fairlight Realty
Construction by Stonegate Build Group
Unveil the height of luxury living with The Aldermoor, a new condo building in East Boston, set for completion in Spring 2025. Experience a standard of elegance and sophistication like never before.
For more information and inquiries, please contact:
Marisol Quennell
Phone: (617) 430-9162
Email: marisol@fairlightprops.com
The banner should be very classy incorporting gold and navy very classic fonts. The Aldermoor should look very classy and exclusive. The stonegate build group logo should be smaller. It should not include their phone number and instagram handle only the name of the company. Herringbone pattern in the background would be great. This is going outside the building to advertise pre construction units

```html
<!DOCTYPE html>
<html lang="en">
<head>
<meta charset="utf-8">
<title>The Aldermoor – Exclusive Luxury Condos</title>
<link rel="stylesheet" href="https://fonts.googleapis.com/css2?family=Cinzel:wght@400;500&family=Montserrat:wght@600;700&family=Questrial&display=swap">
<style>
  :root {
    --navy-deep: #0f1846;
    --navy: #1b2754;
    --ink: #1f2a4d;
    --gold-dark: #c98a16;
    --gold: #f0b52a;
    --gold-light: #fff1a0;
    --white: #ffffff;
    --rule: #c9c9c9;
  }
  * { margin: 0; padding: 0; box-sizing: border-box; }
  html, body { width: 1200px; height: 600px; overflow: hidden; background: var(--white); }

  .banner { position: relative; width: 1200px; height: 600px; overflow: hidden; background: var(--white); }

  .hero {
    position: absolute; left: 0; top: 0; width: 1200px; height: 419px; overflow: hidden;
    background:
      radial-gradient(ellipse 520px 300px at 720px 220px, rgba(60,78,140,0.55), transparent 70%),
      linear-gradient(120deg, var(--navy-deep) 0%, var(--navy) 45%, var(--navy-deep) 100%);
  }
  .hero-stripes { position: absolute; inset: 0; }

  .seal {
    position: absolute; left: -55px; top: -137px; width: 400px; height: 400px; border-radius: 50%;
    background: radial-gradient(circle at 60% 62%, var(--gold-light) 0%, #f7d85a 40%, var(--gold) 75%, var(--gold-dark) 100%);
    box-shadow: 0 0 0 3px #f6c23a;
  }
  .seal-text {
    position: absolute; left: 0; top: 40px; width: 325px; text-align: center;
    font-family: "Cinzel", serif; font-weight: 400; color: var(--ink);
    font-size: 52px; line-height: 53px; letter-spacing: 1px;
  }

  .gold-text {
    background: linear-gradient(180deg, #fff3a6 0%, #f5c536 45%, #d9901a 75%, #f7d458 100%);
    -webkit-background-clip: text; background-clip: text; color: transparent;
  }

  .title-the {
    position: absolute; left: 372px; top: 45px; width: 738px; height: 46px;
    display: flex; align-items: center; gap: 14px;
  }
  .title-the .rule { flex: 1; height: 2px; background: linear-gradient(90deg, var(--gold-dark), var(--gold-light), var(--gold)); margin-top: 4px; }
  .title-the span { font-family: "Cinzel", serif; font-size: 36px; font-weight: 500; line-height: 1; }

  .title-name {
    position: absolute; left: 340px; top: 86px; width: 800px; text-align: center;
    font-family: "Cinzel", serif; font-weight: 400; font-size: 110px; line-height: 1.05; letter-spacing: 2px;
    filter: drop-shadow(2px 3px 3px rgba(0,0,0,0.45));
  }
  .title-sub {
    position: absolute; left: 340px; top: 194px; width: 800px; text-align: center;
    font-family: "Cinzel", serif; font-weight: 400; font-size: 41px; letter-spacing: 1px;
    filter: drop-shadow(2px 2px 2px rgba(0,0,0,0.5));
  }

  .intro {
    position: absolute; left: 260px; top: 276px; width: 900px; text-align: center;
    font-family: "Questrial", sans-serif; color: var(--white); font-size: 26px; line-height: 31px;
  }
  .tagline {
    position: absolute; left: 240px; top: 345px; width: 920px; text-align: center;
    font-family: "Montserrat", sans-serif; font-weight: 600; font-size: 24px;
  }

  .gold-band {
    position: absolute; left: 0; top: 419px; width: 1200px; height: 10px;
    background: linear-gradient(90deg, #b97a14, var(--gold) 30%, var(--gold-light) 55%, var(--gold) 80%, #e7a821);
  }

  .footer { position: absolute; left: 0; top: 429px; width: 1200px; height: 171px; color: var(--ink); }
  .label { font-family: "Montserrat", sans-serif; font-weight: 700; font-size: 15px; letter-spacing: 0.3px; }

  .listed { position: absolute; left: 35px; top: 40px; width: 155px; text-align: center; }
  .listed .agent { font-family: "Montserrat", sans-serif; font-weight: 700; font-size: 24px; line-height: 26px; margin-top: 10px; letter-spacing: -0.5px; }

  .agency {
    position: absolute; left: 205px; top: 50px; width: 220px; height: 60px;
    display: flex; align-items: center; justify-content: center; gap: 12px;
  }
  .agency-dot { width: 40px; height: 40px; border-radius: 50%; background: var(--ink); flex: none; }
  .agency-name { font-family: "Montserrat", sans-serif; font-weight: 700; font-size: 22px; line-height: 25px; color: var(--ink); }

  .divider { position: absolute; top: 28px; width: 2px; height: 117px; background: linear-gradient(180deg, transparent, var(--rule) 20%, var(--rule) 80%, transparent); }
  .divider-a { left: 439px; }
  .divider-b { left: 645px; }

  .builder { position: absolute; left: 452px; top: 28px; width: 182px; text-align: center; }
  .builder-name { margin-top: 36px; font-family: "Montserrat", sans-serif; font-weight: 700; font-size: 15px; line-height: 18px; color: var(--ink); letter-spacing: 0.5px; }

  .contact { position: absolute; left: 670px; top: 29px; width: 510px; text-align: center; }
  .contact .label { font-size: 14.5px; }
  .contact-name { font-family: "Montserrat", sans-serif; font-weight: 700; font-size: 31px; margin-top: 9px; letter-spacing: 0.5px; }
  .contact-lines { display: flex; justify-content: center; align-items: center; gap: 6px; margin-top: 6px; font-family: "Montserrat", sans-serif; font-weight: 700; font-size: 19px; }
  .contact-lines .icon { width: 22px; height: 22px; border-radius: 50%; background: var(--ink); display: inline-flex; align-items: center; justify-content: center; }
  .contact-lines .item { display: inline-flex; align-items: center; gap: 5px; }
</style>
</head>
<body>
<div class="banner">
  <section class="hero">
    <svg class="hero-stripes" width="1200" height="419" viewBox="0 0 1200 419" aria-hidden="true">
      <polygon points="820,0 1000,0 1200,230 1200,419 1140,419" fill="rgba(255,255,255,0.035)"/>
      <polygon points="1040,0 1110,0 1200,105 1200,180" fill="rgba(255,255,255,0.04)"/>
      <polygon points="0,240 0,419 120,419" fill="rgba(255,255,255,0.03)"/>
      <polygon points="0,300 0,340 70,419 110,419" fill="rgba(0,0,0,0.15)"/>
    </svg>

    <div class="seal"></div>
    <div class="seal-text">COMING<br>SPRING<br>2025</div>

    <div class="title-the"><div class="rule"></div><span class="gold-text">THE</span><div class="rule"></div></div>
    <h1 class="title-name gold-text">ALDERMOOR</h1>
    <h2 class="title-sub gold-text">EXCLUSIVE LUXURY CONDOS</h2>

    <p class="intro">Unveil the height of luxury living with The Aldermoor, a new<br>condo building in East Boston, set for completion in Spring 2025.</p>
    <p class="tagline gold-text">Experience a standard of elegance and sophistication like never before.</p>
  </section>

  <div class="gold-band"></div>

  <footer class="footer">
    <div class="listed">
      <div class="label">LISTED BY</div>
      <div class="agent">MARISOL<br>QUENNELL</div>
    </div>

    <div class="agency">
      <span class="agency-dot"></span>
      <span class="agency-name">FAIRLIGHT<br>REALTY</span>
    </div>

    <div class="divider divider-a"></div>

    <div class="builder">
      <div class="label">CONSTRUCTION BY</div>
      <div class="builder-name">STONEGATE<br>BUILD GROUP</div>
    </div>

    <div class="divider divider-b"></div>

    <div class="contact">
      <div class="label">FOR MORE INFORMATION AND INQUIRIES, PLEASE CONTACT</div>
      <div class="contact-name">MARISOL QUENNELL</div>
      <div class="contact-lines">
        <span class="item">
          <span class="icon">
            <svg width="13" height="13" viewBox="0 0 24 24" aria-hidden="true"><path d="M6.6 10.8a15 15 0 0 0 6.6 6.6l2.2-2.2a1 1 0 0 1 1-.25 11.4 11.4 0 0 0 3.6.57 1 1 0 0 1 1 1V20a1 1 0 0 1-1 1A17 17 0 0 1 3 4a1 1 0 0 1 1-1h3.5a1 1 0 0 1 1 1c0 1.25.2 2.45.57 3.57a1 1 0 0 1-.25 1z" fill="#fff"/></svg>
          </span>(617) 430-9162
        </span>
        <span class="item">
          <span class="icon">
            <svg width="13" height="13" viewBox="0 0 24 24" aria-hidden="true"><rect x="3" y="6" width="18" height="12" rx="1.5" fill="none" stroke="#fff" stroke-width="2"/><path d="M3.5 7l8.5 6 8.5-6" fill="none" stroke="#fff" stroke-width="2"/></svg>
          </span>marisol@fairlightprops.com
        </span>
      </div>
    </div>
  </footer>
</div>
</body>
</html>
```